Medical Billing Company Needs a Business Card Design

We need a business card design for a Florida based medical billing company called 'Clinicians Keystone Solutions'. We specialize in providing revenue cycle management services to physician and therapist offices (we're basically their back-office processing partner for providing billing software, claims submissions, A/R follow-up and patient statements & collections. Our logo is red and blue-ish, so make sure that whatever other elements are used will match appropriately. Our current business card design has a too small font size. I'd like to project an image that shows we are modern & reliable. On a side note, I'm planning on using ZUB for printing these cards.

Target Market(s)

Office managers, physicians, therapists

Industry/Entity Type

Printing

Requirements
Must have
• Logo
Name of Employee
Phone
Fax
E-mail
Website

```html
<!DOCTYPE html>
<html lang="en">
<head>
<meta charset="utf-8">
<title>Clinicians Keystone Solutions – Business Card</title>
<link rel="stylesheet" href="https://fonts.googleapis.com/css2?family=Open+Sans:wght@400;600;700&display=swap">
<style>
  :root {
    --navy: #2b2a86;
    --navy-light: #4a47b0;
    --red: #a3151b;
    --red-deep: #8a0d12;
    --red-glow: #c0393e;
    --paper: #ffffff;
    --ink: #3d3d4a;
    --stage: #ece9e4;
  }
  * { box-sizing: border-box; margin: 0; padding: 0; }
  html, body {
    width: 1200px; height: 720px; overflow: hidden;
    background: var(--stage);
    font-family: "Open Sans", sans-serif;
  }
  .canvas {
    position: relative; width: 1200px; height: 720px;
    display: flex; align-items: center; justify-content: center; gap: 40px;
  }
  .card {
    position: relative; width: 540px; height: 309px;
    box-shadow: 0 6px 18px rgba(0,0,0,.18);
    overflow: hidden;
  }

  /* Front */
  .card--front { background: var(--paper); }
  .brand {
    position: absolute; top: 62px; left: 0; right: 0;
    text-align: center; color: var(--navy);
    font-size: 25px; font-weight: 600; letter-spacing: 2.5px;
  }
  .name-band {
    position: absolute; top: 120px; left: 0; right: 0; height: 42px;
    border-top: 2px solid var(--red); border-bottom: 2px solid var(--red);
    padding: 3px 0;
    background: var(--paper);
  }
  .name-band__fill {
    height: 100%;
    background: linear-gradient(90deg, var(--navy) 0%, var(--navy-light) 50%, var(--navy) 100%);
    display: flex; align-items: center; justify-content: flex-end;
    padding-right: 150px;
    color: #fff; font-size: 18px;
  }
  .name-band__fill strong { font-weight: 700; }
  .details {
    position: absolute; top: 190px; left: 0; right: 0;
    display: flex; justify-content: center;
    color: var(--ink); font-size: 13px; line-height: 19px;
  }
  .address {
    text-align: right; padding: 14px 16px 0 0;
    border-right: 1px solid #b9b9c4;
  }
  .contacts { list-style: none; padding-left: 12px; }
  .contacts li { display: flex; align-items: center; gap: 7px; }
  .contacts svg { width: 13px; height: 13px; flex: none; }

  /* Back */
  .card--back {
    background: radial-gradient(ellipse at 45% 40%, var(--red-glow) 0%, var(--red) 45%, var(--red-deep) 100%);
    color: #fff; text-align: center;
  }
  .back-brand {
    position: absolute; top: 100px; left: 0; right: 0;
    font-size: 30px; font-weight: 600; letter-spacing: 3px;
  }
  .back-web {
    position: absolute; top: 176px; left: 0; right: 0;
    font-size: 15px; letter-spacing: 3px;
  }
</style>
</head>
<body>
<main class="canvas">

  <section class="card card--front" aria-label="Card front">
    <div class="brand">CLINICIANS KEYSTONE</div>
    <div class="name-band">
      <div class="name-band__fill"><span><strong>Your Name,</strong>&nbsp;Title</span></div>
    </div>
    <div class="details">
      <address class="address" style="font-style:normal">
        Street Name<br>City Name<br>State Zip Code
      </address>
      <ul class="contacts">
        <li>
          <svg viewBox="0 0 16 16"><circle cx="8" cy="8" r="8" fill="var(--navy)"/><path d="M5 4.5l1.6-.3 1 2-1 .8a5 5 0 0 0 2.4 2.4l.8-1 2 1-.3 1.6c-3.8.3-6.8-2.7-6.5-6.5z" fill="#fff"/></svg>
          123-456-0789
        </li>
        <li>
          <svg viewBox="0 0 16 16"><circle cx="8" cy="8" r="8" fill="var(--navy)"/><rect x="5.5" y="3.5" width="5" height="3" fill="#fff"/><rect x="4" y="6.5" width="8" height="4" rx="1" fill="#fff"/><rect x="5.5" y="9.5" width="5" height="3" fill="#fff" stroke="var(--navy)" stroke-width=".6"/></svg>
          123-456-0789
        </li>
        <li>
          <svg viewBox="0 0 16 16"><circle cx="8" cy="8" r="8" fill="var(--navy)"/><rect x="4" y="5" width="8" height="6" fill="#fff"/><path d="M4 5l4 3.3L12 5" fill="none" stroke="var(--navy)" stroke-width=".9"/></svg>
          info@clinicianskeystone.com
        </li>
        <li>
          <svg viewBox="0 0 16 16"><circle cx="8" cy="8" r="8" fill="var(--navy)"/><g fill="none" stroke="#fff" stroke-width=".9"><circle cx="8" cy="8" r="4.2"/><ellipse cx="8" cy="8" rx="1.8" ry="4.2"/><path d="M3.8 8h8.4"/></g></svg>
          www.clinicianskeystone.com
        </li>
      </ul>
    </div>
  </section>

  <section class="card card--back" aria-label="Card back">
    <div class="back-brand">CLINICIANS KEYSTONE</div>
    <div class="back-web">www.clinicianskeystone.com</div>
  </section>

</main>
</body>
</html>
```